New website for salon services and wedding hair and makeup

I am a professional hairstylist and makeup artist in Charleston, SC. I have my own company where I see clients for cut and color and I also go on site for weddings. I have a current website that I would like to update and change the style. I would like to add a contact form, map, additional pages and be mobile friendly. It is important to me that it have a site map and can show up in searches. I will need to add photos to the site every so often and would like to continue to work with the designer. I have a logo that I am happy with and have attached the file however if you think a new logo would help the look of the site I am open to it. My current website is www.brightcombstudio-example.com, I would like to change the style and layout so it looks up to date. Here are some links to sites that I like the look of but I don't want to limit your creativity. http://willowlanefolio-example.com/ http://www.runwaylensworks-example.com http://miraventhol-example.com/. I have attached a few files for mock up purposes, please let me know if you would like more content. Thank you!

Target Market(s)

Women, Brides

Industry/Entity Type

Hair And Beauty

Number of Pages Required

1 page

Font styles to use
Sans Serif
Script

Requirements
Must have
• Contact form, Mobile friendly, sitemap
Nice to have
• I really like the look for the sites I have included on the project description guide.
Should not have
• Nothing overly girly.

```html
<!DOCTYPE html>
<html lang="en">
<head>
<meta charset="utf-8">
<title>Brightcomb Studio – Hair & Makeup</title>
<link href="https://fonts.googleapis.com/css2?family=Roboto:wght@300;400;500&family=Great+Vibes&display=swap" rel="stylesheet">
<style>
:root{
  --teal:#3fb4bd;
  --teal-soft:#a9e3e7;
  --teal-band:rgba(120,214,220,.85);
  --ink:#444;
  --muted:#8a8a8a;
  --rule:#d9d9d9;
  --footer:#ececec;
  --bg:#fff;
}
*{box-sizing:border-box;margin:0;padding:0}
html,body{width:698px;height:1200px;overflow:hidden;background:var(--bg)}
body{position:relative;font-family:'Roboto',Arial,sans-serif;color:var(--ink)}
.abs{position:absolute}

.nav{left:0;top:0;width:698px;height:24px;border-bottom:1px solid var(--rule);display:flex;justify-content:center;gap:4px}
.nav a{font-size:6.5px;letter-spacing:.5px;color:#555;text-decoration:none;padding:0 16px;line-height:23px}
.nav a.active{background:var(--teal-soft);color:#fff}

.connect{left:42px;top:58px;display:flex;align-items:center;gap:5px;font-size:6.5px;color:#666}
.social{display:flex;gap:4px}
.social span{width:12px;height:12px;border:1px solid #999;border-radius:50%}
.brand{left:249px;top:38px;width:200px;height:50px;display:flex;align-items:center;justify-content:center;gap:8px}
.brand .dot{width:14px;height:14px;background:var(--teal-soft);border-radius:50%}
.brand b{font-weight:400;font-size:20px;color:var(--teal)}
.contact{right:42px;top:58px;display:flex;gap:12px;font-size:6.5px;color:#666}
.contact svg{vertical-align:-2px;margin-right:3px}

.hero{left:42px;top:108px;width:614px;height:244px;background:linear-gradient(110deg,#2e3236 0%,#7b6a55 40%,#c7a57d 60%,#3b3a36 100%)}
.hero-caption{left:42px;top:288px;width:290px;height:44px;background:var(--teal-band);padding:5px 10px}
.hero-caption h1{font-weight:400;font-size:17px;color:#fff;line-height:18px}
.hero-caption p{font-family:'Great Vibes',cursive;font-size:15px;color:#fff;line-height:18px}
.arrows{left:600px;top:302px;display:flex;gap:3px}
.arrows span{width:16px;height:16px;background:#333;display:flex;align-items:center;justify-content:center}

.about-photo{left:42px;top:372px;width:250px;height:160px;background:linear-gradient(90deg,#e9e3dc,#c9a98a 50%,#eee8e2)}
.kicker{font-weight:300;font-size:15px;letter-spacing:1px;color:#666}
.title{font-weight:400;font-size:26px;color:var(--teal);line-height:28px;letter-spacing:.5px}
.about-text{left:304px;top:378px;width:352px}
.about-text p{margin-top:8px;font-size:6.5px;line-height:10px;color:var(--muted)}

.section-head{left:0;width:698px;text-align:center}
.rule{left:42px;width:614px;height:1px;background:var(--rule)}
.services-intro{left:180px;top:640px;width:338px;text-align:center;font-size:6.5px;line-height:10px;color:var(--muted)}
.service{top:684px;width:134px}
.service .btn{height:18px;background:var(--teal-soft);border:1px solid var(--teal);font-size:6.5px;letter-spacing:.3px;color:#fff;text-align:center;line-height:16px;font-weight:500}
.service .photo{margin-top:8px;height:100px}
.dots{left:339px;top:834px;display:flex;gap:4px}
.dots span{width:5px;height:5px;border-radius:50%;background:#bbb}
.dots span.on{background:#555}

.gallery-photo{top:948px;width:192px;height:155px}

.footer{left:42px;top:1128px;width:614px;height:42px;background:var(--footer);display:flex;align-items:center;justify-content:space-between;padding:0 12px;font-size:6px;color:#777}
</style>
</head>
<body>

<nav class="nav abs">
  <a class="active">HOME</a><a>ABOUT</a><a>SERVICES</a><a>GALLERY</a><a>CONTACT</a>
</nav>

<div class="connect abs">CONNECT US
  <div class="social"><span></span><span></span><span></span><span></span></div>
</div>
<div class="brand abs"><span class="dot"></span><b>Brightcomb Studio</b></div>
<div class="contact abs">
  <span><svg width="8" height="8" viewBox="0 0 10 10"><path d="M2 1l2 2-1 1.5c.8 1.5 1.7 2.4 3 3L7.5 6l2 2-1.5 1.5C4 9 1 6 .5 1.5z" fill="#888"/></svg>843 555 0142</span>
  <span><svg width="9" height="7" viewBox="0 0 10 8"><rect x=".5" y=".5" width="9" height="7" fill="none" stroke="#888"/><path d="M.5 .5l4.5 4 4.5-4" fill="none" stroke="#888"/></svg>hello@brightcombstudio-example.com</span>
</div>

<div class="hero abs" role="img" aria-label="Portrait of a woman with styled hair and makeup"></div>
<div class="hero-caption abs">
  <h1>Welcome to Brightcomb Studio</h1>
  <p>Chic. Sophisticated. Inspired</p>
</div>
<div class="arrows abs">
  <span><svg width="6" height="8" viewBox="0 0 6 8"><path d="M5 0L1 4l4 4" fill="none" stroke="#fff"/></svg></span>
  <span><svg width="6" height="8" viewBox="0 0 6 8"><path d="M1 0l4 4-4 4" fill="none" stroke="#fff"/></svg></span>
</div>

<div class="about-photo abs" role="img" aria-label="Makeup artist applying makeup with brushes"></div>
<div class="about-text abs">
  <div class="kicker">BRIGHTCOMB</div>
  <div class="title">HAIR &amp; MAKEUP</div>
  <p>Brightcomb Studio specializes in polished, long lasting hair and makeup for every occasion. With years of salon and bridal experience, we know how to make your day feel effortless. We take pride in client care and listen closely so the look you picture is the look you leave with. Our team travels on site for weddings and events, bringing calm, timing and quality products, so you can enjoy the day with the people you love.</p>
</div>

<div class="rule abs" style="top:556px"></div>
<div class="section-head abs" style="top:580px">
  <div class="kicker">BRIGHTCOMB</div>
  <div class="title">SERVICES</div>
</div>
<p class="services-intro abs">Brightcomb Studio offers cut, color, styling and bridal services. With years of experience and training, we know how to make your day feel easy.</p>

<div class="service abs" style="left:42px"><div class="btn">BRIDAL</div><div class="photo" role="img" aria-label="Bride with an elegant updo" style="background:linear-gradient(135deg,#f3efe9,#cbb59a)"></div></div>
<div class="service abs" style="left:202px"><div class="btn">HAIR CUT</div><div class="photo" role="img" aria-label="Stylist cutting a client's hair" style="background:linear-gradient(135deg,#3a3e44,#9aa3aa)"></div></div>
<div class="service abs" style="left:362px"><div class="btn">HAIR COLOR</div><div class="photo" role="img" aria-label="Colorist applying hair dye" style="background:linear-gradient(135deg,#e6dccf,#a88866)"></div></div>
<div class="service abs" style="left:522px"><div class="btn">STYLING AND TREATMENTS</div><div class="photo" role="img" aria-label="Client receiving a styling treatment" style="background:linear-gradient(135deg,#efe8e0,#b99a80)"></div></div>

<div class="dots abs"><span class="on"></span><span></span></div>

<div class="rule abs" style="top:866px"></div>
<div class="section-head abs" style="top:884px">
  <div class="kicker">BRIGHTCOMB</div>
  <div class="title">GALLERY</div>
</div>

<div class="gallery-photo abs" role="img" aria-label="Stylist preparing a bride's hair" style="left:42px;background:linear-gradient(135deg,#ded6cc,#7d6a5a)"></div>
<div class="gallery-photo abs" role="img" aria-label="Bride with finished makeup" style="left:253px;background:linear-gradient(135deg,#b8a18a,#5b4536)"></div>
<div class="gallery-photo abs" role="img" aria-label="Bride with veil and styled hair" style="left:464px;background:linear-gradient(135deg,#f4f1ed,#c8b4a2)"></div>

<footer class="footer abs">
  <span>Copyright © 2024 Brightcomb Studio. All Rights Reserved</span>
  <div class="social"><span></span><span></span><span></span><span></span></div>
</footer>

</body>
</html>
```